Design my site www.brieflyledger.com

So here is what I am thinking in terms of design:

https://plenvo.com

https://www.skyluxair.com

http://kalvex.com/harbor-plaza-tower/

I want the theme to be white and blue (royal blue). I attached a paint picture of what I would like the site to look like in terms of placing the text. Generally, what I like about the sites above is that they are simple, you can navigate easily and have some kind of idea of what's going on by looking at the center (picture and motto). Let's establish a clear understanding of how the functional part of the site would look like. Please see the picture attached.

I want to keep it simple: On top would be the Name 'BRIEFLY ledger", somewhere to the right on top on the page would be 'Sign in" button.

In the center would be a picture (maybe a video) with the Motto (on top of it all in capital) OBSERVE NAVIGATE DECIDE and below would be the "sign up now"

Below the picture (like on kalvex.com site) or to the left on top of the page would be "About Us', "Press" "Contact Us' buttons.

Then once the user gets to his page his got 3 tabs " Press Headlines", "Events", " Briefings".

we would keep the same format I only have on the site, but separate for every Tab.

I do not want the user to get distracted. I also want him to be able to access the page though mobile phone and be able to get automatic updates just like Zorvan Pings without having to sign in daily.

The landing page must be minimalist yet with business/corporate feel where users can navigate easily and a "what you see is what you get" approach. You want an image or video (personally I prefer the video.. it does capture the users attention instantly, as long as it is an interesting video), with your taglines in it.

Sections available to public: About Us, Contact Us, Landing Page with Signup Option

Private: Public Sections + User Account Page, Tabs for (Events, Press Headlines, Briefings)

Target Market(s)

PR/media monitoring/diplomatic community

Coding

Coded - Design and coding required

Number of Pages Required

1 page

Font styles to use
Serif
Sans Serif

Colors
0255a3
ec1f27

Requirements
Must have
• a simple landing page, that is user friendly.
Nice to have
• a video with the explanation of how to navigate the site
Should not have
• too many colors, graphs etc.

```html
<!DOCTYPE html>
<html lang="en">
<head>
<meta charset="utf-8">
<title>Briefly Ledger</title>
<link href="https://fonts.googleapis.com/css2?family=Arimo:wght@400;700&family=Open+Sans:wght@400;600&display=swap" rel="stylesheet">
<style>
  :root {
    --blue: #0255a3;
    --red: #ec1f27;
    --page: #f8f8f8;
    --panel: #e8e8e8;
    --panel-head: #dadada;
    --rule: #cfcfcf;
    --ink: #111111;
    --muted: #7a7a7a;
    --footer: #333333;
    --white: #ffffff;
  }
  * { box-sizing: border-box; margin: 0; padding: 0; }
  html, body { width: 1200px; height: 714px; overflow: hidden; }
  body {
    position: relative;
    background: var(--page);
    font-family: "Open Sans", Arial, sans-serif;
    color: var(--ink);
  }

  /* Top bar */
  .topbar {
    position: absolute; left: 0; top: 0; width: 1200px; height: 62px;
    background: var(--white); border-bottom: 1px solid #dcdcdc;
  }
  .menu-toggle {
    position: absolute; left: 0; top: 0; width: 69px; height: 61px;
    background: var(--page); border-right: 1px solid #dcdcdc;
    display: flex; align-items: center; justify-content: center;
  }
  .brand {
    position: absolute; left: 92px; top: 18px;
    font-family: "Arimo", Arial, sans-serif; font-weight: 700;
    font-size: 22px; letter-spacing: 0.5px; color: var(--blue);
  }
  .social {
    position: absolute; left: 883px; top: 0; width: 189px; height: 61px;
    background: var(--page); border-left: 1px solid #dcdcdc;
    display: flex; align-items: center; justify-content: center; gap: 1px;
  }
  .social span { width: 30px; height: 30px; background: var(--blue); display: block; }
  .sign-in {
    position: absolute; left: 1072px; top: 0; width: 128px; height: 61px;
    background: var(--blue); color: var(--white);
    font-family: "Arimo", Arial, sans-serif; font-weight: 700; font-size: 14px;
    display: flex; align-items: center; justify-content: center;
  }

  /* Panels */
  .panel {
    position: absolute; top: 152px; width: 333px; height: 413px;
    background: var(--panel);
  }
  .panel--headlines { left: 91px; }
  .panel--events { left: 434px; }
  .panel--briefing { left: 775px; }
  .panel-title {
    height: 63px; background: var(--panel-head); border-bottom: 1px solid var(--rule);
    font-family: "Arimo", Arial, sans-serif; font-weight: 700; font-size: 19px;
    letter-spacing: 0.3px; padding: 20px 0 0 30px;
  }
  .panel--events .panel-title { padding-left: 27px; }
  .track { position: absolute; width: 1px; background: #b8b8b8; }
  .thumb { position: absolute; width: 4px; }

  /* Headlines */
  .headline { position: absolute; left: 31px; width: 280px; height: 80px; }
  .headline-photo { position: absolute; left: 0; top: 0; width: 81px; height: 71px; }
  .headline-body { position: absolute; left: 99px; top: -4px; width: 185px; }
  .item-title { font-size: 12.5px; color: var(--ink); }
  .item-text { font-size: 10.5px; line-height: 17px; color: var(--muted); margin-top: 1px; }
  .meta { font-size: 11.5px; color: var(--ink); margin-top: 2px; }
  .meta .time { display: inline-block; margin-left: 12px; position: relative; top: 9px; font-size: 12px; }
  .meta .venue { font-size: 10.5px; color: #555; margin-left: 5px; position: relative; top: 9px; }

  /* Events */
  .event-photo { position: absolute; left: 23px; top: 93px; width: 285px; height: 122px; }
  .event-body { position: absolute; left: 23px; top: 233px; width: 270px; }
  .event-body .item-title { font-size: 13px; }
  .event-body .item-text { font-size: 12.5px; line-height: 15px; margin-top: 5px; }
  .event-meta { margin-top: 14px; font-size: 14px; }
  .event-meta .time { margin-left: 20px; font-size: 15px; }
  .event-meta .venue { margin-left: 8px; font-size: 13px; color: #555; }
  .button {
    position: absolute; left: 23px; top: 338px; width: 139px; height: 41px;
    background: var(--red); color: var(--white); font-size: 14px;
    display: flex; align-items: center; justify-content: center;
  }

  /* Briefing */
  .briefing-list { list-style: none; position: absolute; left: 35px; top: 99px; }
  .briefing-list li {
    position: relative; padding-left: 22px; width: 270px; height: 49px;
    font-size: 14px; line-height: 16px; color: var(--muted);
  }
  .briefing-list li::before {
    content: ""; position: absolute; left: 0; top: 4px;
    width: 10px; height: 10px; border-radius: 50%; background: var(--blue);
  }

  /* Footer */
  .footer {
    position: absolute; left: 0; top: 658px; width: 1200px; height: 56px;
    background: var(--footer); color: #dddddd;
    font-family: "Arimo", Arial, sans-serif; font-size: 12px;
    display: flex; align-items: center; justify-content: center;
  }
</style>
</head>
<body>
  <header class="topbar">
    <div class="menu-toggle">
      <svg width="24" height="14" viewBox="0 0 24 14" aria-hidden="true">
        <rect y="0" width="24" height="3" fill="#ec1f27"/>
        <rect y="5.5" width="24" height="3" fill="#ec1f27"/>
        <rect y="11" width="24" height="3" fill="#ec1f27"/>
      </svg>
    </div>
    <div class="brand">BRIEFLY LEDGER</div>
    <nav class="social" aria-label="Social links">
      <span></span><span></span><span></span><span></span><span></span>
    </nav>
    <a class="sign-in">SING IN</a>
  </header>

  <section class="panel panel--headlines">
    <h2 class="panel-title">NEWS PAPERS HEADLINES</h2>
    <article class="headline" style="top:95px">
      <div class="headline-photo" role="img" aria-label="News anchor at a studio desk" style="background:linear-gradient(135deg,#3b4f8c,#7a6a73)"></div>
      <div class="headline-body">
        <div class="item-title">Lorem ipsum dolor sit amet,</div>
        <div class="item-text">Duis autem vel eum iriure dolor in hendrerit invulputate velit.</div>
        <div class="meta">Jan 05, 2016 <span class="time">Time</span><span class="venue">Venue</span></div>
      </div>
    </article>
    <article class="headline" style="top:192px">
      <div class="headline-photo" role="img" aria-label="Portrait of a young man outdoors" style="background:linear-gradient(135deg,#9fb07a,#c9a688)"></div>
      <div class="headline-body">
        <div class="item-title">Lorem ipsum dolor sit amet,</div>
        <div class="item-text">Duis autem vel eum iriure dolor in hendrerit invulputate velit.</div>
        <div class="meta">Jan 05, 2016 <span class="time">Time</span><span class="venue">Venue</span></div>
      </div>
    </article>
    <article class="headline" style="top:289px">
      <div class="headline-photo" role="img" aria-label="News presenter in a blue studio" style="background:linear-gradient(135deg,#2a4a9e,#d9896a)"></div>
      <div class="headline-body">
        <div class="item-title">Lorem ipsum dolor sit amet,</div>
        <div class="item-text">Duis autem vel eum iriure dolor in hendrerit invulputate velit.</div>
        <div class="meta">Jan 05, 2016 <span class="time">Time</span><span class="venue">Venue</span></div>
      </div>
    </article>
    <div class="track" style="left:319px;top:92px;height:313px"></div>
    <div class="thumb" style="left:317px;top:92px;height:102px;background:var(--red)"></div>
  </section>

  <section class="panel panel--events">
    <h2 class="panel-title">EVENTS</h2>
    <div class="event-photo" role="img" aria-label="Close-up of calendar pages" style="background:linear-gradient(120deg,#e9e9e9,#bdbdbd 60%,#e6e6e6)"></div>
    <div class="event-body">
      <div class="item-title">Lorem ipsum dolor sit amet,</div>
      <div class="item-text">Duis autem vel eum iriure dolor in hendrerit invulp utate velit.</div>
      <div class="meta event-meta">Jan 05, 2014 <span class="time" style="top:0">Time</span><span class="venue" style="top:0">Venue</span></div>
    </div>
    <a class="button">OUR EVENTS</a>
    <div class="track" style="left:321px;top:106px;height:284px"></div>
    <div class="thumb" style="left:319px;top:106px;height:82px;background:var(--blue)"></div>
  </section>

  <section class="panel panel--briefing">
    <h2 class="panel-title">DAILY BRIEFING</h2>
    <ul class="briefing-list">
      <li>Duis autem vel eum iriure dolor in hendrerit invulp utate velit.</li>
      <li>Duis autem vel eum iriure dolor in hendrerit invulp utate velit.</li>
      <li>Duis autem vel eum iriure dolor in hendrerit invulp utate velit.</li>
      <li>Duis autem vel eum iriure dolor in hendrerit invulp utate velit.</li>
      <li>Duis autem vel eum iriure dolor in hendrerit invulp utate velit.</li>
      <li>Duis autem vel eum iriure dolor in hendrerit invulp utate velit.</li>
    </ul>
  </section>

  <footer class="footer">COPYRIGHT © 2016 BRIEFLYLEDGER.</footer>
</body>
</html>
```